Kestrel Facilities Business Card Design

We would now like to design business cards with the new Kestrel Facilities logo

Target Market(s)

Professional

Industry/Entity Type

Professional services

Contact Information for Business Card

Employee name, title, phone number, email address, corporate office address and logo.

Font styles to use
Sans Serif

Colors
0054AA
0677BA
7BADD7
CADEEF
E8F1F8

Requirements
Must have
• My logo
Should not have
• any other pictures or images besides my logo

```html
<!DOCTYPE html>
<html lang="en">
<head>
<meta charset="utf-8">
<title>Kestrel Facilities — Business Card</title>
<link rel="stylesheet" href="https://fonts.googleapis.com/css2?family=Montserrat:wght@700&family=Quicksand:wght@500;600&display=swap">
<style>
  :root {
    --brand-blue: #3476bd;
    --brand-deep: #2f6fb8;
    --mark-silver: #cdd3e3;
    --ink: #1b1b1b;
    --paper: #ffffff;
    --backdrop: #2a2a2a;
  }
  * { margin: 0; padding: 0; box-sizing: border-box; }
  html, body { width: 1200px; height: 960px; overflow: hidden; }
  body {
    background: var(--backdrop);
    display: flex;
    flex-direction: column;
    align-items: center;
    justify-content: center;
    gap: 64px;
    font-family: "Quicksand", sans-serif;
  }
  .card {
    width: 620px;
    height: 354px;
    border-radius: 22px;
    position: relative;
    overflow: hidden;
  }
  .card--front { background: var(--brand-blue); display: flex; align-items: center; justify-content: center; }
  .card--back { background: var(--paper); display: flex; align-items: center; padding: 0 40px 0 44px; }
  .brand {
    display: flex; align-items: center; gap: 14px;
    font-family: "Montserrat", sans-serif; font-weight: 700;
    letter-spacing: 0.01em; line-height: 1.05;
  }
  .brand__square { width: 34px; height: 34px; flex: none; }
  .card--front .brand { color: var(--mark-silver); font-size: 40px; }
  .card--front .brand__square { background: var(--mark-silver); width: 44px; height: 44px; }
  .card--back .brand { color: var(--brand-deep); font-size: 30px; width: 250px; }
  .card--back .brand__square { background: var(--brand-deep); }
  .divider { width: 2px; height: 190px; background: var(--brand-deep); margin: 0 30px 0 16px; flex: none; }
  .contact { color: var(--ink); font-size: 14.5px; font-weight: 500; }
  .contact__name { font-family: "Montserrat", sans-serif; font-weight: 700; color: var(--brand-deep); font-size: 21px; letter-spacing: 0.01em; }
  .contact__title { font-size: 16px; font-weight: 600; margin: 2px 0 14px; }
  .contact__address { line-height: 1.35; margin-bottom: 12px; }
  .contact__list { list-style: none; line-height: 1.5; }
  .contact__list li { display: flex; align-items: center; gap: 8px; }
  .contact__list svg { width: 13px; height: 13px; fill: var(--brand-deep); flex: none; }
</style>
</head>
<body>
  <section class="card card--front">
    <div class="brand"><span class="brand__square"></span><span>Kestrel<br>Facilities</span></div>
  </section>

  <section class="card card--back">
    <div class="brand"><span class="brand__square"></span><span>Kestrel<br>Facilities</span></div>
    <div class="divider"></div>
    <div class="contact">
      <p class="contact__name">NYAMBURA ACHIENG</p>
      <p class="contact__title">Co-Founder</p>
      <p class="contact__address">P.O Box 4810-00200<br>Nairobi, Kenya</p>
      <ul class="contact__list">
        <li><svg viewBox="0 0 16 16" aria-hidden="true"><path d="M1 5c0-2 3-3 7-3s7 1 7 3v1h-4V5H5v1H1zM3 8h10l1 6H2z"/></svg>+254-700-41275</li>
        <li><svg viewBox="0 0 16 16" aria-hidden="true"><path d="M1 3h14v10H1zM2 4l6 5 6-5z" fill-rule="evenodd"/></svg>info@kestrelfacilities.com</li>
        <li><svg viewBox="0 0 16 16" aria-hidden="true"><circle cx="8" cy="8" r="7"/></svg>www.kestrelfacilities.com</li>
      </ul>
    </div>
  </section>
</body>
</html>
```